New Business Card Design Project

I need a design for business cards, i am an electrical business called "Corvane Electrical and Communications" i need the cards to be double sided with the company logo on the back (attached) the front needs to say my company name, web site, email address, telephone number, and ABN number and electrical license number. I am open to different arrangements of the information but would like the background to be incorporating something electrical or something that looks smart. open to all additional ideas also.

The company colours are orange and grey see logo attached.

Business Name: Corvane Electrical and Communications
Website: corvaneelectricalandcomms.example.com.au
Email: brent@corvaneelectricalandcomms.example.com.au
Telephone(mobile): 0481209736
ABN: 71208349162
Lic No: 418273D

Target Market(s)

Business entities, Project Managers, Accounts, Clients

Industry/Entity Type

Electrician

Contact Information for Business Card

I need a design for business cards, i am an electrical business called "Corvane Electrical and Communications" i need the cards to be double sided with the company logo on the back (attached) the front needs to say my company name

Font styles to use
Serif
Sans Serif

Colors
f37122
5c5c5c

Requirements
Must have
• Must have the Logo on the back open to different ways of it being on the back but had in mind to keep it central but again open to other options
Nice to have
• A real modern cool background that is eye catching yet contemporary
Should not have
• No backgrounds of a light bulb or plug or anything like that

```html
<!DOCTYPE html>
<html lang="en">
<head>
<meta charset="utf-8">
<title>Corvane Electrical and Communications – Business Card</title>
<link rel="stylesheet" href="https://fonts.googleapis.com/css2?family=Roboto:wght@400;700&display=swap">
<style>
  :root {
    --orange: #f37122;
    --grey: #5c5c5c;
    --card-dark: #3a3a3a;
    --card-mid: #4b4b4b;
    --panel-light: #d4d4d4;
    --stripe-white: #f2f2f2;
    --text-light: #f4f4f4;
    --text-dark: #4a4a4a;
    --backdrop: #dcdcdc;
  }
  * { box-sizing: border-box; margin: 0; padding: 0; }
  html, body { width: 1200px; height: 950px; overflow: hidden; }
  body {
    background: var(--backdrop);
    font-family: "Roboto", Arial, sans-serif;
  }
  .canvas {
    position: relative;
    width: 1200px;
    height: 950px;
    overflow: hidden;
  }
  .card {
    position: absolute;
    left: 220px;
    width: 760px;
    height: 434px;
    border-radius: 6px;
    overflow: hidden;
    background: linear-gradient(135deg, var(--card-mid) 0%, var(--card-dark) 100%);
    box-shadow: 0 10px 24px rgba(0,0,0,0.25);
  }
  .card--back { top: 34px; }
  .card--front { top: 490px; }

  /* Brand name block */
  .brand {
    display: flex;
    align-items: center;
    gap: 16px;
  }
  .brand__dot {
    flex: none;
    width: 20px;
    height: 20px;
    border-radius: 50%;
    background: var(--orange);
  }
  .brand__name {
    color: var(--orange);
    font-weight: 700;
    line-height: 1.15;
    text-transform: uppercase;
    letter-spacing: 0.02em;
  }

  /* Back side */
  .back__brand {
    position: absolute;
    left: 0; right: 0;
    top: 140px;
    justify-content: center;
  }
  .back__brand .brand__name { font-size: 34px; width: 440px; }
  .back__web {
    position: absolute;
    left: 0; right: 0;
    top: 278px;
    text-align: center;
    color: #cfcfcf;
    font-size: 18px;
    letter-spacing: 0.02em;
  }

  /* Front side */
  .front__brand {
    position: absolute;
    left: 42px;
    top: 150px;
  }
  .front__brand .brand__name { font-size: 25px; width: 270px; }
  .front__divider {
    position: absolute;
    left: 368px;
    top: 50px;
    width: 1px;
    height: 250px;
    background: rgba(255,255,255,0.35);
  }
  .contact {
    position: absolute;
    left: 392px;
    top: 58px;
    color: var(--text-light);
    font-size: 17px;
    line-height: 1.45;
  }
  .contact__name {
    color: var(--orange);
    font-weight: 700;
    font-size: 24px;
    line-height: 1.2;
  }
  .contact__role { font-size: 18px; margin-bottom: 8px; }
  .contact__row { display: flex; align-items: center; gap: 9px; }
  .contact__row svg { flex: none; }
  .contact__email { font-size: 14px; }

  .front__bands {
    position: absolute;
    left: 0; top: 0;
  }
  .front__web {
    position: absolute;
    right: 24px;
    top: 382px;
    color: var(--text-dark);
    font-size: 19px;
    letter-spacing: 0.01em;
  }
</style>
</head>
<body>
<main class="canvas">

  <section class="card card--back" aria-label="Business card, back">
    <div class="brand back__brand">
      <span class="brand__dot"></span>
      <span class="brand__name">Corvane Electrical and Communications</span>
    </div>
    <p class="back__web">corvaneelectricalandcomms.example.com.au</p>
  </section>

  <section class="card card--front" aria-label="Business card, front">
    <svg class="front__bands" width="760" height="434" viewBox="0 0 760 434" aria-hidden="true">
      <polygon points="0,330 128,330 122,344 0,344" fill="var(--orange)"/>
      <polygon points="134,330 232,330 226,344 128,344" fill="var(--stripe-white)"/>
      <polygon points="238,330 338,330 332,344 232,344" fill="var(--orange)"/>
      <polygon points="344,330 760,330 760,434 300,434" fill="var(--panel-light)"/>
    </svg>

    <div class="brand front__brand">
      <span class="brand__dot"></span>
      <span class="brand__name">Corvane Electrical and Communications</span>
    </div>

    <div class="front__divider"></div>

    <div class="contact">
      <p class="contact__name">Liam Harte</p>
      <p class="contact__role">President</p>
      <p>ABN: 71208349162</p>
      <p>Lic No: 418273D</p>
      <p class="contact__row">
        <svg width="13" height="19" viewBox="0 0 13 19" aria-hidden="true">
          <rect x="1" y="1" width="11" height="17" rx="2" fill="none" stroke="var(--orange)" stroke-width="2"/>
          <circle cx="6.5" cy="14.5" r="1.2" fill="var(--orange)"/>
        </svg>
        0481209736
      </p>
      <p class="contact__row contact__email">
        <svg width="16" height="12" viewBox="0 0 16 12" aria-hidden="true">
          <rect x="0" y="0" width="16" height="12" rx="1" fill="var(--orange)"/>
          <polyline points="1,1 8,7 15,1" fill="none" stroke="var(--card-dark)" stroke-width="1.5"/>
        </svg>
        brent@corvaneelectricalandcomms.example.com.au
      </p>
    </div>

    <p class="front__web">corvaneelectricalandcomms.example.com.au</p>
  </section>

</main>
</body>
</html>
```